Business cards for Harbourline Supply Pty Ltd that import building products into Australia from China
Target Market(s)
Business to Business
Industry/Entity Type
Business
Contact Information for Business Card
Front: Logo and Business Name
Rear:
Desmond Varrick
General Manager
Mobile: 0427 561 394
email: dessie@harbourlinesupply.com.au
alternative email: dessie@outbackworks.com.au
web: www.harbourlinesupply.com.au
Adelaide, Brisbane and Darwin
Colors
ec1f27
fbee3d

```html
<!DOCTYPE html>
<html lang="en">
<head>
<meta charset="utf-8">
<title>Harbourline Supply – Business Cards</title>
<link rel="stylesheet" href="https://fonts.googleapis.com/css2?family=Arimo:wght@400&family=Barlow+Semi+Condensed:wght@400;600&display=swap">
<style>
  :root {
    --brand-red: #e31c24;
    --brand-yellow: #fedd00;
    --ink-white: #ffffff;
    --backdrop: #ececec;
  }
  * { margin: 0; padding: 0; box-sizing: border-box; }
  html, body {
    width: 1200px;
    height: 448px;
    overflow: hidden;
    background: var(--backdrop);
  }
  .canvas {
    position: relative;
    width: 1200px;
    height: 448px;
  }
  .card {
    position: absolute;
    top: 67px;
    width: 548px;
    height: 313px;
  }
  .card--rear {
    left: 40px;
    background: var(--brand-red);
    color: var(--ink-white);
  }
  .card--front {
    left: 611px;
    background: var(--brand-yellow);
    display: flex;
    align-items: center;
    justify-content: center;
  }
  .identity {
    position: absolute;
    top: 53px;
    left: 0;
    width: 100%;
    text-align: center;
    font-family: "Barlow Semi Condensed", sans-serif;
    line-height: 1;
  }
  .identity__name {
    font-weight: 600;
    font-size: 26px;
    letter-spacing: 0.2px;
  }
  .identity__role {
    margin-top: 3px;
    font-weight: 400;
    font-size: 19px;
  }
  .contacts {
    position: absolute;
    left: 116px;
    top: 128px;
    list-style: none;
    font-family: "Arimo", sans-serif;
    font-size: 19px;
    line-height: 25px;
  }
  .contact {
    position: relative;
    padding-left: 40px;
    white-space: nowrap;
  }
  .contact--phone { margin-bottom: 20px; }
  .contact--email { margin-bottom: 9px; }
  .contact__icon {
    position: absolute;
    left: 0;
    top: -2px;
    width: 29px;
    height: 29px;
  }
  .brand-name {
    font-family: "Arimo", sans-serif;
    font-weight: 400;
    font-size: 52px;
    color: var(--brand-red);
    letter-spacing: -0.5px;
    margin-top: -14px;
  }
</style>
</head>
<body>
<main class="canvas">
  <section class="card card--rear" aria-label="Business card rear">
    <header class="identity">
      <p class="identity__name">DESMOND VARRICK</p>
      <p class="identity__role">GENERAL MANAGER</p>
    </header>
    <ul class="contacts">
      <li class="contact contact--phone">
        <svg class="contact__icon" viewBox="0 0 29 29" aria-hidden="true">
          <circle cx="14.5" cy="14.5" r="14.5" fill="#fff"/>
          <rect x="9.5" y="6" width="10" height="17" rx="2" fill="#e31c24"/>
          <rect x="11" y="8" width="7" height="11" fill="#fff"/>
          <circle cx="14.5" cy="21" r="0.9" fill="#fff"/>
        </svg>
        0427 561 394
      </li>
      <li class="contact contact--email">
        <svg class="contact__icon" viewBox="0 0 29 29" aria-hidden="true">
          <circle cx="14.5" cy="14.5" r="14.5" fill="#fff"/>
          <rect x="7.5" y="9.5" width="14" height="10" rx="1.2" fill="#e31c24"/>
          <path d="M8 10.5 L14.5 15.5 L21 10.5" fill="none" stroke="#fff" stroke-width="1.4"/>
        </svg>
        dessie@harbourlinesupply.com.au<br>
        dessie@outbackworks.com.au
      </li>
      <li class="contact contact--web">
        <svg class="contact__icon" viewBox="0 0 29 29" aria-hidden="true">
          <circle cx="14.5" cy="14.5" r="14.5" fill="#fff"/>
          <g fill="none" stroke="#e31c24" stroke-width="1.2">
            <circle cx="14.5" cy="14.5" r="7"/>
            <ellipse cx="14.5" cy="14.5" rx="3" ry="7"/>
            <line x1="7.5" y1="14.5" x2="21.5" y2="14.5"/>
            <line x1="8.5" y1="11" x2="20.5" y2="11"/>
            <line x1="8.5" y1="18" x2="20.5" y2="18"/>
          </g>
        </svg>
        www.harbourlinesupply.com.au
      </li>
    </ul>
  </section>
  <section class="card card--front" aria-label="Business card front">
    <p class="brand-name">harbourline supply</p>
  </section>
</main>
</body>
</html>
```